VelkaVision.com

Complete Website Design (Godaddy) and company Branding / Logo Design. The products will sell are only done in-person and are installed. So this site does not need to be an e-commerce site. We will only be giving out information and collecting customer inquires. Website will only need to be about 3 to 5 pages.

```html
<!DOCTYPE html>
<html lang="en">
<head>
<meta charset="utf-8">
<title>VelkaVision</title>
<link rel="stylesheet" href="https://fonts.googleapis.com/css2?family=Open+Sans:wght@400;600&family=Poppins:wght@400;500;600;700&family=Roboto:wght@400&display=swap">
<style>
:root{
  --green:#00e05a;
  --ink:#222226;
  --text:#555;
  --line:#d9d9d9;
  --white:#fff;
}
*{box-sizing:border-box;margin:0;padding:0}
html,body{width:1200px;height:2322px;overflow:hidden;background:var(--white)}
body{position:relative;font-family:'Poppins',sans-serif;color:var(--ink)}
.abs{position:absolute}
.hero{left:0;top:0;width:1200px;height:620px;
  background:linear-gradient(180deg,#e4e3e8 0%,#e9e8ec 60%,#d9d1c8 78%,#e8e1d9 100%)}
.hero-scene{left:540px;top:140px;width:660px;height:440px;
  background:linear-gradient(90deg,rgba(20,20,24,0) 0%,rgba(20,20,24,.08) 10%,rgba(30,30,36,.35) 30%,rgba(40,60,140,.25) 70%,rgba(40,70,180,.35) 100%);border-radius:6px}
.logo{font-family:'Open Sans',sans-serif;font-weight:400;font-size:40px;color:var(--ink);line-height:1;white-space:nowrap}
.menu{left:1058px;top:47px;width:31px;height:23px}
.welcome{left:111px;top:228px;font-family:'Open Sans',sans-serif;font-size:33px;color:var(--ink);line-height:1}
.hero-title{left:108px;top:278px;font-family:'Open Sans',sans-serif;font-weight:400;font-size:70px;color:var(--ink);line-height:1;white-space:nowrap}
.btn-solid{left:111px;top:379px;width:135px;height:54px;background:var(--green);color:var(--ink);
  font-weight:600;font-size:15px;display:flex;align-items:center;justify-content:center;border-radius:2px}
.dots{left:578px;top:585px;display:flex;gap:8px}
.dots span{width:10px;height:10px;border-radius:50%;background:#9a9a9a}
.dots span.on{background:var(--green)}
.about-photo{left:111px;top:715px;width:490px;height:388px}
.eyebrow{font-weight:600;font-size:18px;color:var(--green);line-height:1;display:flex;align-items:center;gap:8px}
.eyebrow i{display:block;width:38px;height:2px;background:linear-gradient(90deg,var(--green),rgba(0,224,90,0))}
.about-eyebrow{left:669px;top:725px}
.h2{font-weight:700;font-size:32px;color:var(--ink);line-height:1}
.about-title{left:669px;top:764px;white-space:nowrap}
.about-text{left:669px;top:820px;width:420px;font-family:'Open Sans',sans-serif;font-size:14px;line-height:24px;color:var(--text);text-align:justify}
.btn-outline{border:2px solid var(--green);color:var(--ink);font-weight:600;font-size:15px;display:flex;align-items:center;justify-content:center;background:transparent;border-radius:2px}
.about-btn{left:669px;top:1037px;width:135px;height:54px}
.contact{left:0;top:1196px;width:1200px;height:626px;
  background:linear-gradient(90deg,#e6e6e6 0%,#ececec 40%,#e8e8e8 70%,#e3e3e3 100%)}
.contact-eyebrow{left:0;top:1261px;width:1200px;justify-content:center}
.contact-eyebrow i:first-child{background:linear-gradient(270deg,var(--green),rgba(0,224,90,0))}
.contact-title{left:0;top:1305px;width:1200px;text-align:center}
.field{background:var(--white);border-radius:6px;font-family:'Roboto',sans-serif;font-size:14px;color:#666;padding:22px 22px}
.submit{left:542px;top:1701px;width:117px;height:54px}
.rule{height:1px;background:var(--line)}
.card{top:1990px;width:307px;height:108px;border:1px solid #cfcfcf;background:var(--white)}
.card .icon{position:absolute;left:7px;top:7px;width:92px;height:92px;background:var(--green);display:flex;align-items:center;justify-content:center}
.card h3{position:absolute;left:119px;font-weight:500;font-size:18px;line-height:1;color:var(--ink)}
.card p{position:absolute;left:119px;font-size:12.5px;line-height:19px;color:var(--ink);white-space:nowrap}
.nav{top:2178px;right:112px;display:flex;gap:50px;font-size:15.5px;color:var(--ink);line-height:1}
.legal{top:2273px;font-size:14px;color:var(--ink);line-height:1}
</style>
</head>
<body>

<header class="abs hero" role="img" aria-label="Photo of a technician installing a TV on a white media console"></header>
<div class="abs hero-scene" role="img" aria-label="Technician kneeling beside a large flat TV"></div>
<div class="abs logo" style="left:109px;top:36px">VelkaVision</div>
<svg class="abs menu" viewBox="0 0 31 23" aria-label="Menu"><g stroke="#666" stroke-width="2"><line x1="0" y1="1" x2="31" y2="1"/><line x1="0" y1="11.5" x2="31" y2="11.5"/><line x1="0" y1="22" x2="31" y2="22"/></g></svg>
<div class="abs welcome">WELCOME TO</div>
<h1 class="abs hero-title">VELKAVISION</h1>
<div class="abs btn-solid">GET STARTED</div>
<div class="abs dots"><span></span><span class="on"></span><span></span></div>

<section>
  <svg class="abs about-photo" viewBox="0 0 490 388" role="img" aria-label="Technician mounting a TV while a customer watches">
    <defs><linearGradient id="aboutTone" x1="0" y1="0" x2="1" y2="1"><stop offset="0" stop-color="#d8d4d0"/><stop offset=".5" stop-color="#8f94a6"/><stop offset="1" stop-color="#c9c4bd"/></linearGradient></defs>
    <polygon points="2,7 488,24 488,359 2,383" fill="url(#aboutTone)"/>
    <polygon points="1,1 489,17 489,364 1,387" fill="none" stroke="#00e05a" stroke-width="1.5"/>
  </svg>
  <div class="abs eyebrow about-eyebrow">ABOUT US <i></i></div>
  <h2 class="abs h2 about-title">Technician Installing a TV</h2>
  <p class="abs about-text">Lorem ipsum dolor sit amet, consectetur adipiscing elit, sed do eiusmod tempor incididunt ut labore et dolore magna aliqua. Ut enim ad minim veniam, quis nostrud exercitation ullamco laboris nisi ut aliquip ex ea commodo consequat. Duis aute irure dolor in reprehenderit in voluptate velit esse cillum dolore eu fugiat nulla pariatur. Excepteur sint occaecat cupidatat non proident, sunt in culpa qui officia deserunt mollit anim id est laborum</p>
  <div class="abs btn-outline about-btn">GET STARTED</div>
</section>

<section>
  <div class="abs contact" role="img" aria-label="Faded photo of a technician beside a TV"></div>
  <div class="abs eyebrow contact-eyebrow"><i></i>CONTACT US<i></i></div>
  <h2 class="abs h2 contact-title">Get In Touch</h2>
  <div class="abs field" style="left:204px;top:1379px;width:384px;height:63px">First Name</div>
  <div class="abs field" style="left:612px;top:1379px;width:384px;height:63px">Last Name</div>
  <div class="abs field" style="left:204px;top:1471px;width:384px;height:64px">Email</div>
  <div class="abs field" style="left:612px;top:1471px;width:384px;height:64px">Phone</div>
  <div class="abs field" style="left:204px;top:1565px;width:792px;height:107px">Message</div>
  <div class="abs btn-outline submit">SUBMIT</div>
</section>

<div class="abs rule" style="left:114px;top:1925px;width:978px"></div>

<div class="abs card" style="left:126px">
  <div class="icon"><svg width="44" height="58" viewBox="0 0 44 58" fill="none" stroke="#fff" stroke-width="3"><path d="M22 55C22 55 3 33 3 21a19 19 0 0 1 38 0c0 12-19 34-19 34z"/><circle cx="22" cy="21" r="7"/></svg></div>
  <h3 style="top:26px">Reach Us</h3>
  <p style="top:50px">123,Lorem ipsum dolor sit<br>amet, conse adipiscing</p>
</div>
<div class="abs card" style="left:451px">
  <div class="icon"><svg width="56" height="56" viewBox="0 0 56 56" fill="none" stroke="#fff" stroke-width="3" stroke-linejoin="round"><path d="M14 4l9 12-5 6c3 7 9 13 16 16l6-5 12 9-5 9C26 51 5 30 5 9z"/></svg></div>
  <h3 style="top:34px">Call Us</h3>
  <p style="top:56px;font-size:14px">+1 (555) 014 2736</p>
</div>
<div class="abs card" style="left:775px">
  <div class="icon"><svg width="58" height="40" viewBox="0 0 58 40" fill="none" stroke="#fff" stroke-width="3" stroke-linejoin="round"><rect x="2" y="2" width="54" height="36"/><path d="M2 2l27 22 27-22M2 38l20-18M56 38L36 20"/></svg></div>
  <h3 style="top:34px">Email Us</h3>
  <p style="top:58px">info@VelkaVision.com</p>
</div>

<footer>
  <div class="abs logo" style="left:114px;top:2166px">VelkaVision</div>
  <nav class="abs nav"><span>HOME</span><span>ABOUT US</span><span>SERVICES</span><span>CONTACT US</span></nav>
  <div class="abs rule" style="left:106px;top:2242px;width:978px"></div>
  <div class="abs legal" style="left:106px">© 2024 VelkaVision &nbsp;|&nbsp;&nbsp; All Rights Reserved</div>
  <div class="abs legal" style="right:116px;display:flex;gap:19px"><span>Privacy Policy</span><span>Terms &amp; Conditions</span></div>
</footer>

</body>
</html>
```